Ward Compass Business Card Design*

We need a business card design for our company Ward Compass. Our company is specialized in providing online consulting services regarding medical institutions, hospitals and doctors. We work with patients worldwide looking to choose between healthcare providers. We have a website you may use as a reference, where we list doctors and clinics worldwide. So we target Medical providers as well as patients worldwide.
Target Market(s)
Medical Providers and patients around the world
Industry/Entity Type
Medical
Contact Information for Business Card
Salwa Kettani
CEO
+90 612 348 2175
info@wardcompass.example
www.wardcompass.example
14 Annakhil 7 H.R.B. Rabat, Morocco
Requirements
Must have
- Company logo/name on one full side, personal info and smaller logo and company name on the other side.
Nice to have
- Smart and elegant design

```html
<!DOCTYPE html>
<html lang="en">
<head>
<meta charset="utf-8">
<title>Ward Compass — Business Card</title>
<link rel="stylesheet" href="https://fonts.googleapis.com/css2?family=Open+Sans:wght@400;700&display=swap">
<style>
  :root {
    --navy: #1d3f6e;
    --grey: #7b7c7e;
    --ink: #2b2b2b;
    --paper: #ffffff;
    --backdrop: #e6e7e9;
    --soft-circle: #e9edf3;
  }
  * { box-sizing: border-box; margin: 0; padding: 0; }
  html, body {
    width: 1200px; height: 768px; overflow: hidden;
    background: var(--backdrop);
    font-family: "Open Sans", Arial, sans-serif;
  }
  .sheet {
    width: 1200px; height: 768px;
    display: flex; align-items: center; justify-content: center; gap: 40px;
  }
  .card {
    position: relative;
    width: 540px; height: 309px;
    background: var(--paper);
    box-shadow: 0 2px 10px rgba(0,0,0,0.12);
    overflow: hidden;
  }

  /* Brand side */
  .brand-side .brand {
    position: absolute; left: 0; right: 0; top: 110px;
    display: flex; align-items: center; justify-content: center; gap: 14px;
  }
  .brand-dot {
    width: 38px; height: 38px; border-radius: 50%;
    background: var(--navy);
  }
  .wordmark {
    font-weight: 700; font-size: 30px; letter-spacing: 1px;
    color: var(--navy); text-transform: uppercase;
  }
  .brand-side .site {
    position: absolute; left: 0; right: 0; bottom: 44px;
    text-align: center; font-size: 13px; letter-spacing: 7px;
    color: var(--ink);
  }

  /* Info side */
  .info-side .wordmark {
    position: absolute; left: 36px; top: 30px;
    font-size: 21px;
  }
  .person { position: absolute; left: 36px; top: 90px; }
  .person .name { font-weight: 700; font-size: 19px; color: var(--navy); line-height: 1.1; }
  .person .role { font-size: 13px; color: var(--ink); }
  .address {
    position: absolute; left: 36px; top: 146px;
    font-size: 14px; line-height: 1.3; color: var(--ink); font-style: normal;
  }
  .contacts {
    position: absolute; left: 36px; top: 196px; list-style: none;
    font-size: 14px; line-height: 1.35; color: var(--ink);
  }
  .contacts li { display: flex; align-items: center; gap: 7px; }
  .contacts svg { width: 12px; height: 12px; fill: var(--navy); flex: none; }
  .big-circle {
    position: absolute; right: 34px; top: 58px;
    width: 200px; height: 200px; border-radius: 50%;
    background: var(--soft-circle);
  }
</style>
</head>
<body>
<main class="sheet">
  <section class="card brand-side" aria-label="Card front">
    <div class="brand">
      <span class="brand-dot"></span>
      <span class="wordmark">Ward Compass</span>
    </div>
    <p class="site">www.wardcompass.example</p>
  </section>

  <section class="card info-side" aria-label="Card back">
    <span class="wordmark">Ward Compass</span>
    <div class="person">
      <p class="name">Salwa Kettani</p>
      <p class="role">CEO</p>
    </div>
    <address class="address">14 Annakhil 7<br>H.R.B. Rabat, Morocco</address>
    <ul class="contacts">
      <li>
        <svg viewBox="0 0 12 12" aria-hidden="true"><path d="M2.5 1h2l1 2.5-1.3 1a6 6 0 0 0 3.3 3.3l1-1.3L11 7.5v2A1.5 1.5 0 0 1 9.5 11 8.5 8.5 0 0 1 1 2.5 1.5 1.5 0 0 1 2.5 1z"/></svg>
        +90 612 348 2175
      </li>
      <li>
        <svg viewBox="0 0 12 12" aria-hidden="true"><path d="M0 2h12v8H0z M0 2l6 4.5L12 2" /><path d="M1 3l5 3.7L11 3v-.5H1z" fill="#fff"/></svg>
        info@wardcompass.example
      </li>
      <li>
        <svg viewBox="0 0 12 12" aria-hidden="true"><circle cx="6" cy="6" r="6"/><path d="M1 6h10M6 1c-2 2.5-2 7.5 0 10M6 1c2 2.5 2 7.5 0 10" stroke="#fff" stroke-width="0.9" fill="none"/></svg>
        www.wardcompass.example
      </li>
    </ul>
    <span class="big-circle"></span>
  </section>
</main>
</body>
</html>
```